Box Truck Wrap design with images and our logo

We need a design for the side of our box truck. We are an HVAC and Plumbing Company serving commercial and residential markets and want something catchy, not too busy but more than just logos. Maybe some equipment and/or verbiage of what we do. Real images would be a bonus. We want people to recognize our brand, see our story on the side of this tuck, much like a billboard, and be motivated to contact us for service.

Target Market(s)

Residential homeowners who need HVAC and Plumbing Services

Industry/Entity Type

Commercial and Residential HVAC

Font styles to use
Other font styles liked:
• Calibri

Colors
0054AA
0677BA
7BADD7
CADEEF
E8F1F8

Requirements
Must have
• Our logo, visible interpretation of what we do - Here is our website - www.fenwickpipeworks.example
Nice to have
• Integrated, easy design
Should not have
• Must not be too busy

```html
<!DOCTYPE html>
<html lang="en">
<head>
<meta charset="utf-8">
<title>Fenwick Pipeworks – Box Truck Side Wrap</title>
<link href="https://fonts.googleapis.com/css2?family=Montserrat:wght@700;800&family=Oswald:wght@500&display=swap" rel="stylesheet">
<style>
  :root {
    --brand-deep: #0054AA;
    --brand-mid: #0677BA;
    --brand-royal: #2a4fa8;
    --brand-light: #7BADD7;
    --brand-pale: #CADEEF;
    --panel-white: #E8F1F8;
    --ink: #111418;
    --stage: #4a6785;
  }
  * { margin: 0; padding: 0; box-sizing: border-box; }
  html, body { width: 1200px; height: 902px; overflow: hidden; }
  body { background: var(--stage); position: relative; }

  .wrap-panel {
    position: absolute; left: 80px; top: 151px;
    width: 1040px; height: 600px; overflow: hidden;
    background: linear-gradient(180deg, #f3f6fa 0%, var(--panel-white) 60%, #d9e3ee 100%);
  }
  .wrap-panel .shapes { position: absolute; inset: 0; }

  .brand {
    position: absolute; left: 70px; top: 150px; width: 580px;
  }
  .brand-name {
    display: flex; align-items: center; gap: 18px;
    font-family: "Montserrat", sans-serif; font-weight: 800;
    font-size: 96px; line-height: 1; letter-spacing: -2px;
    color: var(--brand-royal);
  }
  .brand-dot {
    width: 44px; height: 44px; border-radius: 50%;
    background: var(--brand-royal); flex: none;
  }
  .brand-tagline {
    margin-top: 10px; text-align: right;
    font-family: "Montserrat", sans-serif; font-weight: 800;
    font-size: 28px; line-height: 1.02; color: var(--ink);
  }

  .contact {
    position: absolute; left: 170px; top: 390px; width: 520px;
    text-align: center; font-family: "Oswald", sans-serif; font-weight: 500;
    color: var(--ink);
  }
  .contact-phone { font-size: 30px; letter-spacing: 0.3px; }
  .contact-social {
    display: flex; justify-content: center; gap: 22px;
    margin-top: 6px; font-size: 21px;
  }
  .contact-social span { display: flex; align-items: center; gap: 8px; }
  .social-dot { width: 26px; height: 26px; border-radius: 50%; background: var(--ink); }
  .contact-web { margin-top: 8px; font-size: 23px; }
</style>
</head>
<body>
  <section class="wrap-panel" aria-label="Box truck side wrap">
    <svg class="shapes" viewBox="0 0 1040 600" width="1040" height="600">
      <!-- top band -->
      <path d="M0 0 H1040 V115 L0 140 Z" fill="var(--brand-royal)"/>
      <path d="M0 0 H1040 V40 C700 45 400 60 0 95 Z" fill="var(--brand-deep)" opacity="0.35"/>
      <!-- lower sweeping bands -->
      <path d="M0 600 V470 C300 480 620 440 1040 330 V600 Z" fill="var(--brand-royal)"/>
      <path d="M0 600 V505 C320 510 650 470 1040 380 V600 Z" fill="var(--panel-white)"/>
      <path d="M0 600 V525 C340 530 680 490 1040 400 V600 Z" fill="var(--brand-royal)"/>
      <path d="M180 600 C480 560 760 500 1040 440 V470 C760 530 520 575 330 600 Z" fill="var(--brand-light)"/>
      <path d="M0 600 V570 C400 575 700 540 1040 480 V500 C720 560 420 590 120 600 Z" fill="var(--panel-white)"/>
      <path d="M640 460 C800 430 920 400 1040 360 V372 C920 412 800 444 660 470 Z" fill="var(--panel-white)"/>

      <!-- service photo tiles -->
      <g stroke="var(--ink)" stroke-width="6" stroke-linejoin="round">
        <polygon role="img" aria-label="Photo of a commercial ceiling with installed ductwork"
          points="760,45 860,40 905,128 855,215 755,220 710,132" fill="#b89a6c"/>
        <polygon role="img" aria-label="Promotional graphic: get the right size HVAC system"
          points="915,150 1015,145 1060,233 1010,320 910,325 865,237" fill="#2b2c33"/>
        <polygon role="img" aria-label="Photo of a hand adjusting a wall thermostat"
          points="725,220 825,215 870,303 820,390 720,395 675,307" fill="#d8c8b4"/>
        <polygon role="img" aria-label="Photo of a technician servicing an air conditioning unit"
          points="860,335 960,330 1005,418 955,505 855,510 810,422" fill="#c9ccd2"/>
      </g>
    </svg>

    <div class="brand">
      <div class="brand-name"><span class="brand-dot"></span>Fenwick</div>
      <div class="brand-tagline">PIPEWORKS HEATING<br>&amp; AIR CONDITIONING</div>
    </div>

    <div class="contact">
      <div class="contact-phone">24/7 HEATING &amp; COOLING: (555) 013-0147</div>
      <div class="contact-social">
        <span><i class="social-dot"></i>fenwickpipeworks</span>
        <span><i class="social-dot"></i>fenwickheating</span>
      </div>
      <div class="contact-web">www.fenwickpipeworks.example</div>
    </div>
  </section>
</body>
</html>
```